Telecommunications/Power civil contractor needs business card design

Were a new telecommunications/power underground civil contractor that is looking for a new business card design. Our company colours are silver or grey and orange. Feel free to use the white background logo or the black background logo.

Target Market(s)

Local contractors, utility companies, private sector mining/energy companies, developers.

Industry/Entity Type

Telecommunications

Contact Information for Business Card

Each card will need the following info:
Persons name:
Title:
E-mail:
Phone number:
Shop Address:
Mailing Address:

Requirements
Must have
• Each card will need the following info:
• Persons name:
• Title:
• E-mail:
• Phone number:
• Shop Address:
• Mailing Address:

```html
<!DOCTYPE html>
<html lang="en">
<head>
<meta charset="utf-8">
<title>Kestrel Line Contracting Inc – Business Card</title>
<link rel="stylesheet" href="https://fonts.googleapis.com/css2?family=Arimo:wght@400;700&display=swap">
<style>
  :root {
    --stage: #2b2b2d;
    --card: #050505;
    --orange: #f2622a;
    --grey: #8a8a8a;
    --white: #f4f4f4;
    --rule: #3a3a3a;
  }
  * { box-sizing: border-box; margin: 0; padding: 0; }
  html, body { width: 1200px; height: 925px; overflow: hidden; }
  body {
    background: var(--stage);
    font-family: "Arimo", Arial, sans-serif;
    display: flex;
    align-items: center;
    justify-content: center;
    gap: 60px;
  }
  .card {
    width: 520px;
    height: 298px;
    background: var(--card);
    position: relative;
    box-shadow: 0 6px 18px rgba(0,0,0,.45);
  }
  /* back side: mark + contact details */
  .card-back {
    display: flex;
    align-items: center;
    padding: 0 36px;
  }
  .back-mark {
    width: 140px;
    display: flex;
    flex-direction: column;
    align-items: center;
    gap: 12px;
    flex: none;
  }
  .mark-circle {
    width: 70px; height: 70px;
    border-radius: 50%;
    border: 5px solid var(--orange);
  }
  .mark-name {
    color: var(--grey);
    font-weight: 700;
    font-size: 13px;
    letter-spacing: 1px;
    text-transform: uppercase;
    text-align: center;
    line-height: 1.3;
  }
  .divider {
    width: 1px;
    height: 230px;
    background: var(--rule);
    margin: 0 26px 0 16px;
    flex: none;
  }
  .contact { color: var(--white); font-size: 14px; line-height: 1.35; }
  .contact-name { color: var(--orange); font-weight: 700; font-size: 16px; }
  .contact-title { margin-bottom: 10px; }
  .contact-company { margin-bottom: 2px; }
  .contact-address { margin-bottom: 2px; }
  .contact-address:last-of-type { margin-bottom: 8px; }
  .address-label { color: var(--orange); }
  .contact-line { display: flex; align-items: center; gap: 8px; }
  .contact-line svg { width: 13px; height: 13px; fill: var(--orange); flex: none; }
  /* front side: centred mark and company name */
  .card-front {
    display: flex;
    flex-direction: column;
    align-items: center;
    justify-content: center;
    gap: 18px;
  }
  .front-circle {
    width: 84px; height: 84px;
    border-radius: 50%;
    border: 6px solid var(--orange);
  }
  .front-name {
    color: var(--grey);
    font-weight: 700;
    font-size: 24px;
    letter-spacing: 2px;
    text-transform: uppercase;
    text-align: center;
    line-height: 1.2;
  }
</style>
</head>
<body>
  <section class="card card-back">
    <div class="back-mark">
      <div class="mark-circle"></div>
      <div class="mark-name">Kestrel Line</div>
    </div>
    <div class="divider"></div>
    <div class="contact">
      <p class="contact-name">Marlow Hayes</p>
      <p class="contact-title">Managing Director</p>
      <p class="contact-company">Kestrel Line Contracting Inc</p>
      <p class="contact-address"><span class="address-label">Shop:</span> 12 Sample Road, Kelmore 0145</p>
      <p class="contact-address"><span class="address-label">Mail:</span> PO Box 88, Kelmore 0145</p>
      <p class="contact-line">
        <svg viewBox="0 0 16 16" aria-hidden="true"><path d="M3 1h3l1.5 4-2 1.3a9 9 0 0 0 4.2 4.2L11 8.5l4 1.5v3a2 2 0 0 1-2 2A12 12 0 0 1 1 3a2 2 0 0 1 2-2z"/></svg>
        555.201.384
      </p>
      <p class="contact-line">
        <svg viewBox="0 0 16 16" aria-hidden="true"><path d="M1 3h14v10H1z M2 4l6 5 6-5" stroke="#050505" stroke-width="1.2"/></svg>
        info@kestrellineinc.com
      </p>
    </div>
  </section>

  <section class="card card-front">
    <div class="front-circle"></div>
    <div class="front-name">Kestrel Line<br>Contracting Inc</div>
  </section>
</body>
</html>
```